Lumavento business card

We need a modern business card - With our 4 colors - See web: www.lumavento.dk

I have attached logo and som old business Cards we have - Lets Make the new ones shine...:-) -

Industry/Entity Type

Business

Requirements
Must have
• the logo with lumavento only,

```html
<!DOCTYPE html>
<html lang="da">
<head>
<meta charset="utf-8">
<title>Lumavento business card</title>
<link rel="stylesheet" href="https://fonts.googleapis.com/css2?family=Source+Sans+3:wght@300;400;600&family=Quicksand:wght@400&display=swap">
<style>
  :root {
    --backdrop: #e4e4e4;
    --card-dark: #000000;
    --card-purple: #722474;
    --purple-deep: #5e1a60;
    --orange: #f7941d;
    --magenta: #e0218a;
    --lime: #b5d334;
    --soft-white: #e6e6e6;
  }
  * { margin: 0; padding: 0; box-sizing: border-box; }
  html, body { width: 1200px; height: 900px; overflow: hidden; }
  body {
    background: var(--backdrop);
    font-family: "Source Sans 3", "Myriad Pro", sans-serif;
    position: relative;
  }
  .card {
    position: absolute;
    top: 306px;
    width: 440px;
    height: 271px;
    border-radius: 12px;
  }
  .card--front { left: 149px; background: var(--card-dark); }
  .card--back { left: 608px; background: var(--card-purple); }

  .brand {
    position: absolute;
    left: 31px;
    width: 176px;
    top: 136px;
    text-align: center;
  }
  .brand__name {
    font-weight: 300;
    font-size: 17px;
    letter-spacing: 3px;
    color: var(--soft-white);
    display: inline-flex;
    align-items: center;
    gap: 7px;
  }
  .brand__dot {
    width: 8px; height: 8px; border-radius: 50%;
    background: var(--lime);
  }
  .brand__rule {
    height: 2px;
    background: var(--lime);
    margin-top: 8px;
  }
  .brand__tagline {
    margin-top: 8px;
    font-size: 11px;
    color: var(--soft-white);
  }

  .contact {
    position: absolute;
    left: 229px;
    top: 58px;
  }
  .contact__name {
    font-weight: 600;
    font-size: 17px;
    color: var(--orange);
    line-height: 20px;
  }
  .contact__role {
    font-size: 12.5px;
    color: var(--magenta);
    line-height: 16px;
  }
  .contact__address {
    margin-top: 18px;
    font-size: 12.5px;
    line-height: 16px;
    color: var(--lime);
  }
  .contact__list {
    list-style: none;
    margin-top: 14px;
    font-size: 12.5px;
    color: var(--lime);
  }
  .contact__list li {
    display: flex;
    align-items: center;
    height: 18.5px;
  }
  .contact__icon {
    width: 10px; height: 10px;
    margin-right: 8px;
    margin-left: 2px;
    fill: var(--orange);
  }

  .back__mark {
    position: absolute;
    left: 0; right: 0;
    top: 102px;
    text-align: center;
    font-family: "Source Sans 3", sans-serif;
    font-weight: 300;
    font-size: 34px;
    letter-spacing: 4px;
    color: var(--purple-deep);
  }
  .back__name, .back__role {
    position: absolute;
    left: 0; right: 0;
    text-align: center;
    font-family: "Quicksand", sans-serif;
    font-size: 14px;
    letter-spacing: 1.6px;
    color: var(--soft-white);
  }
  .back__name { top: 181px; }
  .back__rule {
    position: absolute;
    left: 104px; width: 232px;
    top: 203px;
    height: 1.5px;
    background: var(--soft-white);
    opacity: .8;
  }
  .back__role { top: 207px; }
</style>
</head>
<body>
  <section class="card card--front">
    <div class="brand">
      <div class="brand__name"><span class="brand__dot"></span>lumavento</div>
      <div class="brand__rule"></div>
      <p class="brand__tagline">Medier til unge</p>
    </div>

    <div class="contact">
      <h1 class="contact__name">Ronja Halvorsen</h1>
      <p class="contact__role">Salgsdirektør</p>
      <p class="contact__address">Lindevænget 14 - 2100<br>Østerbro -Tlf. 31 40 72 60</p>
      <ul class="contact__list">
        <li>
          <svg class="contact__icon" viewBox="0 0 10 10" aria-hidden="true"><path d="M2 0.5 L3.6 2.6 L2.7 3.6 Q3.6 5.9 6.3 7.3 L7.4 6.4 L9.5 8 L8.4 9.5 Q1.6 8.6 0.5 1.6 Z"/></svg>
          +45 60 12 34 78
        </li>
        <li>
          <svg class="contact__icon" viewBox="0 0 10 10" aria-hidden="true"><path d="M0.5 2 H9.5 V8.5 H0.5 Z M1 2.5 L5 5.6 L9 2.5" stroke="#000" stroke-width="0.8"/></svg>
          rh@lumavento.dk
        </li>
        <li>
          <svg class="contact__icon" viewBox="0 0 10 10" aria-hidden="true"><circle cx="5" cy="5" r="4.6"/><path d="M3 2.5 Q4.5 3.5 3.8 5 Q5.5 6 5 8.5 M6 1.5 Q7 3 8.5 3.5" stroke="#000" stroke-width="0.8" fill="none"/></svg>
          www.lumavento.dk
        </li>
      </ul>
    </div>
  </section>

  <section class="card card--back">
    <div class="back__mark">lumavento</div>
    <p class="back__name">Ronja Halvorsen</p>
    <div class="back__rule"></div>
    <p class="back__role">Salgsdirektør</p>
  </section>
</body>
</html>
```